Condo Debts Collection Business needs a Web Design (Contest)

I need a site for a client, who works with condo debts collection, and ensure all revenues provided by condo fees will be always available to the building manager of condo on a specific date, regardless of defaults.I have the logo of the companies, and some requirements on layout (kind of slider, menu options, phone number on a noble position, etc).
Updates

Designs look the same

Target Market(s)

I have two targets for this design: - Condominium's building manager. This target is looking for a solution to overdue debts on it's condo. - Residents on condominiums. This target wants to live in a better place, where their neighbors pay their condominium fees on time.

Number of Pages Required

1 page

Requirements
Must have
• - Slider with title, some short text related, a nice image (I prefer happy and/or peaceful family, people doing business, happy friends, and so on).
• - I have a special attention to menu. I'm looking for one I can have a nice effect, more elegant, charming, kind of innovative.
• - Phone number on the top (or clearly visible).
• - Member log in area or icon on the top (or clearly visible).
• - News/articles area.
• - Modern fonts, with good quality, sans-serif on areas where reading is more intensive (prefer Google web-fonts).
• - Colors specified on attached files.
• - Header similar or inspired by the "FILE 3"
Nice to have
• - Clear background color, cause it's better to read larger texts (like articles). Dark backgrounds makes reading difficult.
• - A site with effects (like shadows, lines, gradients, lights) is usually pretty.
• - I pay attention on beautiful footers.
Should not have
• - Images with a lot of money (I don't sell richness, I sell tranquility, peace, harmony, safety).
• - Poor menu.
• - Lots of curves. My customer asked for straight lines.

```html
<!DOCTYPE html>
<html lang="en">
<head>
<meta charset="utf-8">
<title>Serenvia</title>
<link rel="stylesheet" href="https://fonts.googleapis.com/css2?family=Montserrat:wght@400;500;600;700;800&family=Open+Sans:ital,wght@0,400;0,600;0,700;1,700&display=swap">
<style>
:root{
  --navy:#0f3f7c;
  --navy-dark:#0a2b5a;
  --orange:#e8651a;
  --ink:#2a2a2a;
  --muted:#4a4a4a;
  --panel:#ebebeb;
  --footer:#1d1d1d;
  --white:#fff;
}
*{box-sizing:border-box;margin:0;padding:0}
html,body{width:1200px;height:3689px;overflow:hidden}
body{position:relative;background:var(--white);font-family:"Open Sans",Arial,sans-serif;color:var(--ink)}
.abs{position:absolute}

/* header */
.site-header{left:0;top:0;width:1200px;height:140px;background:linear-gradient(180deg,#1a5299 0%,#123f7a 60%,var(--navy-dark) 100%);box-shadow:0 3px 10px rgba(0,0,0,.35);z-index:2}
.brand{left:108px;top:64px;color:var(--white);font:700 27px "Montserrat",sans-serif;letter-spacing:1px}
.brand-mark{left:168px;top:14px;width:42px;height:42px;background:var(--white)}
.brand-tag{left:112px;top:98px;color:#f5a06a;font:400 10px "Open Sans",sans-serif}
.contact-chip{display:flex;align-items:center;gap:12px;color:var(--white);font:400 15px/1.35 "Open Sans",sans-serif}
.contact-chip b{font-weight:700}
.login-btn{left:932px;top:25px;width:177px;height:51px;background:var(--orange);color:var(--white);font:700 15px "Montserrat",sans-serif;display:flex;align-items:center;justify-content:center;gap:8px}
.main-nav{left:342px;top:101px;color:var(--white);font:500 16px "Montserrat",sans-serif}
.main-nav span{position:absolute;white-space:nowrap}
.nav-icon{top:101px}

/* hero */
.hero{left:0;top:140px;width:1200px;height:676px;
  background:
    radial-gradient(ellipse 260px 150px at 520px 330px,rgba(255,246,200,.95),rgba(255,214,120,.6) 45%,rgba(255,190,90,0) 100%),
    linear-gradient(180deg,#7f8f9c 0%,#a9a39a 18%,#d6a866 38%,#f0bd6a 47%,#3f3a22 52%,#5a4a26 60%,#7a5e30 72%,#4a3a1c 86%,#2c2312 100%)}
.hero-square{left:874px;top:248px;width:84px;height:84px;background:var(--navy)}
.hero-name{left:690px;top:448px;color:var(--navy);font:800 74px/1 "Montserrat",sans-serif;letter-spacing:1px}
.hero-tag{left:740px;top:532px;color:var(--orange);font:italic 700 22px "Open Sans",sans-serif}

/* about */
.eyebrow{color:var(--navy);font:700 15px "Montserrat",sans-serif}
.section-title{color:var(--orange);font:700 36px/1.2 "Montserrat",sans-serif}
.title-rule{width:46px;height:3px;background:var(--navy)}
.body-copy{font-size:14.5px;line-height:31px;color:var(--muted)}
.btn-orange{background:var(--orange);color:var(--white);font:700 15px "Montserrat",sans-serif;display:flex;align-items:center;justify-content:center;gap:10px}
.video-frame-navy{left:644px;top:917px;width:502px;height:342px;background:var(--navy)}
.video-frame-orange{left:615px;top:954px;width:496px;height:325px;background:var(--orange)}
.video-photo{left:634px;top:934px;width:495px;height:330px;
  background:
    radial-gradient(ellipse 220px 140px at 250px 120px,rgba(240,214,190,.95),rgba(200,160,130,0) 100%),
    linear-gradient(180deg,#d9d2c8 0%,#c4b2a0 45%,#6b5a4c 70%,#2a2626 100%);
  box-shadow:0 6px 16px rgba(0,0,0,.35)}
.play{left:870px;top:1084px}

/* services */
.services-band{left:0;top:1380px;width:1200px;height:496px;background:var(--panel)}
.services-photo{left:0;top:1380px;width:612px;height:496px;
  background:
    radial-gradient(ellipse 240px 220px at 70px 120px,rgba(255,252,240,1),rgba(240,230,205,.6) 50%,rgba(200,185,160,0) 100%),
    linear-gradient(180deg,#e8e0cf 0%,#b9a98f 40%,#5c5650 70%,#1e1e22 100%)}
.service{width:240px}
.service h4{display:flex;align-items:center;gap:12px;color:var(--orange);font:700 22px "Montserrat",sans-serif}
.service p{margin-top:6px;font-size:13px;line-height:26px;color:var(--muted)}

/* news */
.news-title{left:0;top:1964px;width:1200px;text-align:center;font:700 36px "Montserrat",sans-serif;color:var(--navy)}
.news-title em{font-style:normal;color:var(--orange)}
.card{width:330px}
.card-img{width:330px;height:194px}
.card-date{position:absolute;left:18px;top:179px;height:30px;padding:0 14px;background:var(--navy);color:var(--white);font-size:13px;display:flex;align-items:center;gap:8px}
.card h3{margin-top:38px;color:var(--orange);font:700 21px "Montserrat",sans-serif;white-space:nowrap}
.card p{margin-top:8px;font-size:12.5px;line-height:24px;color:var(--muted)}
.card a{display:block;margin-top:6px;color:var(--orange);font:700 13px "Montserrat",sans-serif;text-decoration:none}

/* contact */
.contact-band{left:0;top:2503px;width:1200px;height:792px;background:#ececec}
.contact-heading{left:0;width:1200px;text-align:center}
.info-icon{width:84px;height:84px;border-radius:50%;background:var(--navy);display:flex;align-items:center;justify-content:center}
.info-text{width:300px;text-align:center;font:600 16.5px/32px "Montserrat",sans-serif;color:#3a3a3a}
.field{background:var(--white);height:34px;padding-left:18px;display:flex;align-items:center;gap:8px;font-size:12px;color:#444}
.field.tall{height:145px;align-items:flex-start;padding-top:10px}

/* footer */
.site-footer{left:0;top:3295px;width:1200px;height:394px;background:var(--footer)}
.foot-brand{left:560px;top:3392px;font:700 30px "Montserrat",sans-serif;color:var(--white)}
.foot-mark{left:498px;top:3386px;width:44px;height:44px;background:var(--white)}
.foot-social{top:3488px;width:32px;height:32px;border:2px solid var(--white);border-radius:50%;display:flex;align-items:center;justify-content:center}
.foot-links{left:0;width:1200px;text-align:center;font:700 15px "Montserrat",sans-serif;color:var(--white)}
.foot-links span{margin:0 14px}
.copyright{left:0;width:1200px;top:3632px;text-align:center;font-size:15px;color:#ddd}
.footer-code{left:1145px;top:3632px;font-size:15px;color:#ddd}
</style>
</head>
<body>

<header class="site-header abs">
  <div class="brand-mark abs"></div>
  <div class="brand abs">SERENVIA</div>
  <div class="brand-tag abs">Our guarantee is your peace</div>

  <div class="contact-chip abs" style="left:430px;top:28px">
    <svg width="40" height="40" viewBox="0 0 40 40"><circle cx="20" cy="20" r="17" fill="none" stroke="#e8651a" stroke-width="3"/><path d="M13 12c2-2 4 2 5 4s-1 3-1 3c1 2 3 4 5 5 0 0 1-2 3-1s6 3 4 5c-3 3-7 2-11-2s-8-9-5-14z" fill="#e8651a"/></svg>
    <div>Support Call us<br><b>1-800 555 0142</b></div>
  </div>
  <div class="contact-chip abs" style="left:664px;top:28px">
    <svg width="42" height="36" viewBox="0 0 42 36"><rect x="3" y="6" width="36" height="26" fill="none" stroke="#e8651a" stroke-width="3"/><path d="M3 6l18 15 18-15" fill="none" stroke="#e8651a" stroke-width="3"/></svg>
    <div>Email us<br><b>info@serenvia.com</b></div>
  </div>
  <div class="login-btn abs">
    <svg width="14" height="16" viewBox="0 0 14 16"><circle cx="7" cy="4" r="4" fill="#fff"/><path d="M0 16c0-5 3-7 7-7s7 2 7 7z" fill="#fff"/></svg>
    MEMBER LOGIN
  </div>

  <nav class="main-nav abs">
    <span style="left:0">HOME</span>
    <span style="left:88px">ABOUT US</span>
    <span style="left:211px">OUR SERVICES</span>
    <span style="left:371px">NEWS/ARTICLES</span>
    <span style="left:541px">CONTACT US</span>
  </nav>
  <svg class="nav-icon abs" style="left:1026px" width="16" height="16" viewBox="0 0 16 16"><rect x="1" y="3" width="14" height="10" fill="none" stroke="#fff" stroke-width="2"/><path d="M1 3l7 6 7-6" fill="none" stroke="#fff" stroke-width="2"/></svg>
  <svg class="nav-icon abs" style="left:1058px" width="16" height="16" viewBox="0 0 16 16"><circle cx="8" cy="8" r="6.5" fill="none" stroke="#fff" stroke-width="2"/><path d="M1.5 8h13M8 1.5c3 3 3 10 0 13M8 1.5c-3 3-3 10 0 13" fill="none" stroke="#fff" stroke-width="1.5"/></svg>
  <svg class="nav-icon abs" style="left:1090px" width="16" height="16" viewBox="0 0 16 16"><circle cx="3" cy="8" r="2.5" fill="#fff"/><circle cx="13" cy="3" r="2.5" fill="#fff"/><circle cx="13" cy="13" r="2.5" fill="#fff"/><path d="M3 8l10-5M3 8l10 5" stroke="#fff" stroke-width="1.5"/></svg>
</header>

<section class="hero abs" role="img" aria-label="Happy family running across a field at sunset, child on the father's shoulders flying a kite"></section>
<div class="hero-square abs"></div>
<div class="hero-name abs">SERENVIA</div>
<div class="hero-tag abs">Our guarantee is your peace of mind</div>

<section class="about">
  <div class="eyebrow abs" style="left:91px;top:932px">WHO WE ARE</div>
  <h2 class="section-title abs" style="left:91px;top:950px">ABOUT US</h2>
  <div class="title-rule abs" style="left:91px;top:1000px"></div>
  <p class="body-copy abs" style="left:91px;top:1010px;width:510px">Sed ut perspiciatis unde omnis iste natus error sit voluptatem accusanti-um doloremque laudantium, totam rem aperiam, eaque ipsa quae ab illo inventore veritatis et quasi architecto beatae vitae dicta sunt explicabo. Nemo enim ipsam voluptatem quia voluptas sit aspernatur aut odit aut fugit, sed quia consequuntur magni dolores eos qui ratione voluptatem sequi nesciunt.</p>
  <div class="btn-orange abs" style="left:91px;top:1212px;width:177px;height:52px">
    <svg width="13" height="16" viewBox="0 0 13 16"><path d="M0 0h8l5 5v11H0z" fill="#fff"/></svg>
    READ MORE
  </div>
  <div class="video-frame-navy abs"></div>
  <div class="video-frame-orange abs"></div>
  <div class="video-photo abs" role="img" aria-label="Smiling family of four relaxing together on a sofa"></div>
  <svg class="play abs" width="26" height="30" viewBox="0 0 26 30"><path d="M2 1l23 14L2 29z" fill="#fff"/></svg>
</section>

<section class="services">
  <div class="services-band abs"></div>
  <div class="services-photo abs" role="img" aria-label="Businessman in a white shirt and tie working at a desk with documents by a bright window"></div>
  <div class="eyebrow abs" style="left:630px;top:1437px">WHAT WE DO</div>
  <h2 class="section-title abs" style="left:630px;top:1458px">OUR SERVICES</h2>
  <div class="title-rule abs" style="left:630px;top:1508px"></div>
  <p class="body-copy abs" style="left:630px;top:1518px;width:530px;font-size:14px">Lorem ipsum dolor sit amet, consectetur adipiscing elit, sed do eiusm tempor incididunt ut labore et dolore magna aliqua. Ut enim ad minim veniam, quis nostrud exercitation consequat.</p>

  <div class="service abs" style="left:630px;top:1622px">
    <h4><svg width="26" height="18" viewBox="0 0 26 18"><rect x="1" y="1" width="24" height="16" fill="none" stroke="#e8651a" stroke-width="2"/><rect x="1" y="5" width="24" height="3" fill="#e8651a"/></svg>LOREM IPSUM</h4>
    <p>Sed ut perspiciatis unde omnis iste natus error sit voluptatem accum</p>
  </div>
  <div class="service abs" style="left:880px;top:1622px">
    <h4><svg width="26" height="18" viewBox="0 0 26 18"><rect x="0" y="0" width="26" height="18" fill="#e8651a"/><rect x="4" y="4" width="8" height="2" fill="#fff"/><rect x="4" y="9" width="18" height="2" fill="#fff"/><rect x="4" y="13" width="12" height="2" fill="#fff"/></svg>LOREM IPSUM</h4>
    <p>Sed ut perspiciatis unde omnis iste natus error sit voluptatem accum</p>
  </div>
  <div class="service abs" style="left:630px;top:1730px">
    <h4><svg width="26" height="18" viewBox="0 0 26 18"><rect x="0" y="0" width="26" height="18" fill="#e8651a"/><circle cx="13" cy="9" r="4" fill="#fff"/></svg>LOREM IPSUM</h4>
    <p>Sed ut perspiciatis unde omnis iste natus error sit voluptatem accum</p>
  </div>
  <div class="service abs" style="left:880px;top:1730px">
    <h4><svg width="26" height="18" viewBox="0 0 26 18"><rect x="1" y="1" width="24" height="16" fill="none" stroke="#e8651a" stroke-width="2"/><circle cx="13" cy="9" r="4" fill="#e8651a"/></svg>LOREM IPSUM</h4>
    <p>Sed ut perspiciatis unde omnis iste natus error sit voluptatem accum</p>
  </div>
</section>

<section class="news">
  <h2 class="news-title abs">NEWS/<em>ARTICLES</em></h2>

  <article class="card abs" style="left:93px;top:2041px">
    <div class="card-img" role="img" aria-label="Family blowing soap bubbles on a sunny lawn" style="background:radial-gradient(ellipse 140px 90px at 120px 90px,rgba(240,220,170,.9),rgba(240,220,170,0)),linear-gradient(180deg,#c9d6a8 0%,#94a85e 50%,#56662c 100%)"></div>
    <div class="card-date"><svg width="12" height="12" viewBox="0 0 12 12"><rect x="0" y="2" width="12" height="10" fill="#fff"/><rect x="0" y="5" width="12" height="1" fill="#0f3f7c"/></svg>Oct 27 2018</div>
    <h3>SED UT PERSPICIATIS UND</h3>
    <p>Sed ut perspiciatis unde omnis iste natus error sit voluptatem accusantium doloremque laudantium, totam rem aperiam, eaque ipsa quae ab illo</p>
    <a>READ MORE</a>
  </article>
  <article class="card abs" style="left:435px;top:2041px">
    <div class="card-img" role="img" aria-label="Parent and child in a cosy play tent lit by warm string lights" style="background:radial-gradient(ellipse 120px 90px at 160px 80px,rgba(255,200,120,.95),rgba(255,170,80,0)),linear-gradient(180deg,#9a5a2a 0%,#6b3a1c 55%,#2e1d14 100%)"></div>
    <div class="card-date"><svg width="12" height="12" viewBox="0 0 12 12"><rect x="0" y="2" width="12" height="10" fill="#fff"/><rect x="0" y="5" width="12" height="1" fill="#0f3f7c"/></svg>Oct 27 2018</div>
    <h3>SED UT PERSPICIATIS UND</h3>
    <p>Sed ut perspiciatis unde omnis iste natus error sit voluptatem accusantium doloremque laudantium, totam rem aperiam, eaque ipsa quae ab illo</p>
    <a>READ MORE</a>
  </article>
  <article class="card abs" style="left:777px;top:2041px">
    <div class="card-img" role="img" aria-label="Happy family posing together in a bright living room" style="background:radial-gradient(ellipse 120px 80px at 200px 110px,rgba(200,150,120,.8),rgba(200,150,120,0)),linear-gradient(180deg,#f6f3ee 0%,#e2d4c6 55%,#a98a72 100%)"></div>
    <div class="card-date"><svg width="12" height="12" viewBox="0 0 12 12"><rect x="0" y="2" width="12" height="10" fill="#fff"/><rect x="0" y="5" width="12" height="1" fill="#0f3f7c"/></svg>Oct 27 2018</div>
    <h3>SED UT PERSPICIATIS UND</h3>
    <p>Sed ut perspiciatis unde omnis iste natus error sit voluptatem accusantium doloremque laudantium, totam rem aperiam, eaque ipsa quae ab illo</p>
    <a>READ MORE</a>
  </article>
</section>

<section class="contact">
  <div class="contact-band abs"></div>
  <h2 class="contact-heading abs" style="top:2564px;font:700 32px Montserrat,sans-serif;color:var(--navy)">CONTACT INFORMATION</h2>
  <div class="contact-heading abs" style="top:2620px;font:500 18px Montserrat,sans-serif;color:#3a3a3a">Contact us for more information</div>

  <div class="info-icon abs" style="left:263px;top:2680px"><svg width="36" height="40" viewBox="0 0 36 40"><path d="M18 3c-6 0-10 4-10 10 0 7 10 18 10 18s10-11 10-18c0-6-4-10-10-10z" fill="none" stroke="#fff" stroke-width="2.5"/><circle cx="18" cy="13" r="4" fill="none" stroke="#fff" stroke-width="2.5"/><path d="M4 30l-2 8h32l-2-8" fill="none" stroke="#fff" stroke-width="2.5"/></svg></div>
  <div class="info-icon abs" style="left:558px;top:2680px"><svg width="38" height="38" viewBox="0 0 40 40"><path d="M9 5c3-3 6 2 7 5s-1 4-1 4c2 4 5 7 9 9 0 0 2-2 4-1s8 4 5 7c-4 4-10 3-16-3S5 10 9 5z" fill="none" stroke="#fff" stroke-width="2.5"/></svg></div>
  <div class="info-icon abs" style="left:873px;top:2680px"><svg width="40" height="30" viewBox="0 0 40 30"><rect x="2" y="2" width="36" height="26" fill="none" stroke="#fff" stroke-width="2.5"/><path d="M2 2l18 14L38 2M2 28l13-13M38 28L25 15" fill="none" stroke="#fff" stroke-width="2.5"/></svg></div>

  <div class="info-text abs" style="left:155px;top:2772px">480 Linden Row,<br>Brookvale, CA 94010</div>
  <div class="info-text abs" style="left:450px;top:2772px">Phone:<br>1-800 555 0142</div>
  <div class="info-text abs" style="left:765px;top:2786px">Email:<br>info@serenvia.com</div>

  <h2 class="contact-heading abs" style="top:2888px;font:700 32px Montserrat,sans-serif;color:var(--orange)">CONTACT US</h2>

  <div class="field abs" style="left:165px;top:2961px;width:425px">&#9679; First Name</div>
  <div class="field abs" style="left:610px;top:2961px;width:428px">&#9679; Last Name</div>
  <div class="field abs" style="left:165px;top:3015px;width:425px">&#9632; Company</div>
  <div class="field abs" style="left:165px;top:3069px;width:425px">&#9993; Email Address</div>
  <div class="field abs" style="left:165px;top:3123px;width:425px">&#9742; Phone Number</div>
  <div class="field tall abs" style="left:610px;top:3015px;width:428px">&#9679; Message :</div>
  <div class="btn-orange abs" style="left:511px;top:3175px;width:178px;height:49px;font-size:16px">
    <svg width="16" height="16" viewBox="0 0 16 16"><path d="M0 7L16 0 12 16 8 10z" fill="#fff"/></svg>
    Submit
  </div>
</section>

<footer class="site-footer abs"></footer>
<div class="foot-mark abs"></div>
<div class="foot-brand abs">SERENVIA</div>
<div class="foot-social abs" style="left:528px"><svg width="14" height="14" viewBox="0 0 16 16"><rect x="1" y="3" width="14" height="10" fill="none" stroke="#fff" stroke-width="2"/><path d="M1 3l7 6 7-6" fill="none" stroke="#fff" stroke-width="2"/></svg></div>
<div class="foot-social abs" style="left:564px"><svg width="14" height="14" viewBox="0 0 16 16"><circle cx="8" cy="8" r="6.5" fill="none" stroke="#fff" stroke-width="2"/><path d="M1.5 8h13M8 1.5c3 3 3 10 0 13M8 1.5c-3 3-3 10 0 13" fill="none" stroke="#fff" stroke-width="1.5"/></svg></div>
<div class="foot-social abs" style="left:600px"><svg width="14" height="14" viewBox="0 0 16 16"><circle cx="3" cy="8" r="2.5" fill="#fff"/><circle cx="13" cy="3" r="2.5" fill="#fff"/><circle cx="13" cy="13" r="2.5" fill="#fff"/><path d="M3 8l10-5M3 8l10 5" stroke="#fff" stroke-width="1.5"/></svg></div>
<div class="foot-social abs" style="left:636px"><svg width="14" height="14" viewBox="0 0 16 16"><path d="M3 12c1-3 3-5 6-5V4l5 5-5 5v-3c-3 0-5 0-6 1z" fill="#fff"/></svg></div>
<div class="foot-links abs" style="top:3543px">
  <span>Home</span>|<span>About Us</span>|<span>Our Services</span>|<span>News/articles</span>|<span>Contact</span>
</div>
<div class="foot-links abs" style="top:3588px">
  <span>Privacy Policy</span>|<span>Terms of Service</span>
</div>
<div class="copyright abs">© 2019 Company Name&nbsp; All right reserved</div>
<div class="footer-code abs">C29</div>

</body>
</html>
```